COMPANY NAME: Bright Harbor Ventures: Task Description: We are a new UK based business with global rea

Target Market

- Personal and professional development – 30-55 age group, corporate leaders, Eastern European and Asian markets
- On-assignment projects – Corporate market – Eastern European and Asian Markets
- Property investment - 35-65 age group, Europe, USA, Australia

What we need

We need logos and brand design for a suite of web platforms (website, twitter and Facebook profile). We would like to have a cohesive and consistent look across all of our online platforms. The design suite must therefore include social media logos, backgrounds and headers. Specifically we are looking for:

a. Facebook header/page design: likely to have a more youthful look

b. Website: Header, background and layout that is responsive to devices, iPhone primarily, then tablet, then PC (we have purchased a website building package from SiteKettle so if you are familiar with one of their themes, it would be great to have a design that fits with a theme you would recommend); Design should be able to accommodate a place to position video in the medium term but an image in the short term.

c. LinkedIn: header/logo; more corporate look

d. Twitter: background/logo

e. Powerpoint template: background and logo - simple and soft background not busy

f. Electronic Newsletter: logo, header and sidebar; simple and soft background not busy

h. Business card: sophisticated and simple

Colors

We have in mind a preference for colors from the purple family, maybe lavender, so as to appeal to all genders and age groups. Though we are happy to go with a recommendation if you think otherwise.

We would like a look that is professional, airy, bright, fresh, futuristic, insightful, friendly.

Ethos of the brand

- experiencing opportunity and being fulfilled in a changing world
- services are facilitated through insights
- support provided through our product, services and tailored approach to coaching/partnerships (which includes private client match-making)
- we are service providers and passionate about quality and modern leadership skills at all stages in life.

The company name is "Bright Harbor Ventures” - our main message is helping people move to the next level - through investments, personal and professional growth.

Some of our messaging

1. International Leadership in a new world.

2. New technology;

3. Informed;

4. Positively Influential

5. Making a difference;

6. Empowered;

7. Risk free investments;

8. Commercial opportunity;

9. Fulfilled living;

10. Carefree and Fun Living;

11. Progression;

12. Open-minded

13. Energy/dynamic

The Business:
The business is to move people very quickly out of situations that hold them back. the situations could be their own personal situations; their career; their jobs; their teams; their ideas; their finances; their financial opportunities. Remove their fears and give them the strategies to take action. The team are international and have 40 years experience between them in this area.

We do want to come across modern and dynamic, customer outcome focussed, building long-term relationships; international.
Updates

Project Deadline Extended
Reason: We have not found the right designs - we are not just looking for a website design but also images and logos. Most images we can see in the designs are stock images - very standard. We need an image which will be the face of the company, like the shop front window. This main image will be used on social media (top image) and also the home page of the website.

Target Market(s)

30-55 years
Eastern Europe; UK; Asia; Africa; Middle East
Personal, Professional, Corporate, and Financial Growth

Industry/Entity Type

Business Service

Contact Information for Business Card

Simple and stylish
the 3 areas of the business on the reverse -

International look - Offices in UK and San Francisco

Company name
web address www.brightharborventure.com
email director@brightharborventure.com
Facebook bright harbor venture
LinkedIn Bright Harbor Venture
Twitter Bright Harbor Venture
Telephone: +44 (0) 768 213 5597

Logo Text

Something that symbolises unlimited growth - probably not text - could use the word INSIGHT in some way

Number of Pages Required

1 page

Colors
e4daeb
f3f1f8
ffffff

Requirements
Must have
• social media symbols and address
• company name
• Melanie Thorpe
• Director
• Telephone +44 (0) 768 213 5597
• Website name www.brightharborventure.co.uk
• Reverse of Card:
• Discreet, Fast, Bright Harbor Consultancy
• Corporate, Professional, Personal & Property Investment
Nice to have
• not too angular; soft lines; not too cluttered (possibly social media on the reverse and just logo, name, number on the front?
Should not have
• too busy

```html
<!DOCTYPE html>
<html lang="en">
<head>
<meta charset="utf-8">
<title>Bright Harbor Venture — Consulting Company</title>
<link rel="stylesheet" href="https://fonts.googleapis.com/css2?family=Open+Sans:wght@400;600;700;800&family=Roboto:wght@400;500;700&display=swap">
<style>
:root{
  --lavender:#e4daeb;
  --mist:#f3f1f8;
  --white:#ffffff;
  --ink:#222222;
  --body:#444444;
  --muted:#666666;
  --footer:#333333;
  --red:#d0202a;
  --purple:#7b6a95;
  --caption:rgba(40,40,45,.82);
}
*{box-sizing:border-box;margin:0;padding:0}
html,body{width:1200px;height:2671px;overflow:hidden}
body{position:relative;background:var(--white);font-family:"Roboto",Arial,sans-serif;color:var(--body)}
.abs{position:absolute}

/* hero */
.hero-photo{left:0;top:0;width:1200px;height:573px;background:linear-gradient(120deg,#cfd9e4 0%,#8ea1b5 35%,#5d6f86 60%,#a9b7c7 100%)}
.site-header{left:110px;top:0;width:980px;height:89px;background:var(--white);border-radius:0 0 46px 46px;box-shadow:0 2px 10px rgba(0,0,0,.08)}
.brand{left:45px;top:22px;display:flex;align-items:center;gap:14px}
.brand-dot{width:48px;height:48px;border-radius:50%;border:2px solid #c8bcd6}
.brand-name{font-family:"Open Sans",Arial,sans-serif;font-size:25px;font-weight:600;color:#333;white-space:nowrap}
.follow-label{left:561px;top:32px;font-size:9px;letter-spacing:.5px;color:#777;white-space:nowrap}
.social{display:flex;gap:8px}
.social span{width:21px;height:21px;border-radius:50%;background:var(--purple)}
.header-social{left:648px;top:28px}
.search{left:782px;top:27px;width:89px;height:28px;border:1px solid #bbb;display:flex;align-items:center;gap:6px;padding-left:10px;font-size:8px;color:#999}
.menu-toggle{left:901px;top:27px;width:36px;height:28px;display:flex;flex-direction:column;justify-content:space-between}
.menu-toggle span{height:2px;background:#999}
.hero-caption{left:659px;top:320px;width:409px;height:125px;background:var(--caption);clip-path:polygon(0 0,100% 0,96% 100%,0 100%);padding:18px 24px 0 32px;color:var(--white)}
.hero-caption h1{font-family:"Open Sans",Arial,sans-serif;font-size:29px;line-height:36px;font-weight:700;letter-spacing:.3px;white-space:nowrap}
.hero-caption p{font-size:13px;line-height:19px;margin-top:6px;width:330px}
.slider-dots{left:532px;top:461px;display:flex;gap:12px;align-items:center}
.slider-dots span{width:9px;height:9px;background:var(--white)}
.slider-dots .active{width:13px;height:13px;background:none;border:2px solid var(--white);border-radius:50%}

/* service cards */
.cards-panel{left:130px;top:513px;width:938px;height:338px;background:var(--white);border-radius:56px}
.card{top:525px;width:292px;height:321px;background:var(--white);border-radius:52px;overflow:hidden;box-shadow:0 2px 8px rgba(0,0,0,.2);text-align:center}
.card-photo{height:168px}
.card h3{font-family:"Open Sans",Arial,sans-serif;font-size:16px;font-weight:600;color:var(--ink);margin-top:22px}
.card p{font-size:12.5px;line-height:19px;color:var(--muted);margin:10px 28px 0}
.read-more{display:inline-block;margin-top:16px;font-size:10.5px;font-weight:700;color:#333;letter-spacing:.3px}

/* features */
.features{left:134px;top:872px;width:934px;height:351px;border-radius:56px;overflow:hidden;background:linear-gradient(100deg,#e8e6ef 40%,#bfc6d6 70%,#eef0f5 100%)}
.features-shade{left:0;top:0;width:420px;height:351px;background:linear-gradient(135deg,#6e6a7c,#85818f);clip-path:polygon(0 0,100% 0,86% 100%,0 100%)}
.features-copy{left:81px;top:50px;width:260px;color:var(--white)}
.features-copy h2{font-family:"Open Sans",Arial,sans-serif;font-size:25px;font-weight:700;text-decoration:underline;text-underline-offset:5px}
.features-copy h4{font-family:"Open Sans",Arial,sans-serif;font-size:16px;font-weight:700;line-height:23px;margin-top:22px}
.features-copy p{font-size:13px;line-height:19.5px;margin-top:14px}
.watch-btn{left:80px;top:248px;width:137px;height:43px;border-radius:22px;background:var(--red);color:var(--white);font-family:"Open Sans",Arial,sans-serif;font-weight:700;font-size:14px;display:flex;align-items:center;justify-content:center}
.play{left:423px;top:107px}

/* welcome */
.welcome{left:134px;top:1245px;width:934px;height:366px;border-radius:56px;overflow:hidden;background:var(--lavender)}
.welcome-photo{left:530px;top:0;width:404px;height:366px;background:linear-gradient(135deg,#e9dccd 0%,#c9b29a 40%,#8ea3b8 75%,#d8d2cc 100%)}
.welcome-copy{left:56px;top:38px;width:436px}
.welcome-copy h2{font-family:"Open Sans",Arial,sans-serif;font-size:19.5px;font-weight:700;color:#333}
.welcome-copy p{font-size:12.6px;line-height:18.7px;color:#555;margin-top:9px;text-align:justify}
.welcome-copy h2+p{margin-top:12px}

/* section headings */
.section-title{left:0;width:1200px;text-align:center;font-family:"Open Sans",Arial,sans-serif;font-weight:700;font-size:18px;color:#333}
.section-title::after{content:"";display:block;width:160px;height:4px;background:var(--lavender);margin:9px auto 0}

/* assignments */
.assignment{top:1704px;width:293px;height:260px;border-radius:56px;overflow:hidden;box-shadow:0 2px 6px rgba(0,0,0,.12)}
.assignment-photo{position:absolute;inset:0}
.assignment-caption{position:absolute;left:0;right:0;top:197px;height:52px;background:rgba(228,218,235,.92);display:flex;align-items:center;justify-content:center;font-family:"Open Sans",Arial,sans-serif;font-weight:600;font-size:16px;color:var(--ink)}
.assignment::after{content:"";position:absolute;left:0;right:0;top:249px;bottom:0;background:var(--mist)}

/* private client */
.private-client{left:0;top:2001px;width:1200px;height:360px;background:var(--mist)}
.service-icon{top:2116px;width:138px;height:138px;border-radius:50%;background:var(--lavender);display:flex;align-items:center;justify-content:center}
.service-label{top:2272px;width:260px;text-align:center;font-size:14px;line-height:20px;color:#333}

/* footer */
.site-footer{left:0;top:2361px;width:1200px;height:267px;background:var(--footer);color:var(--white)}
.footer-brand{left:130px;top:71px;display:flex;align-items:center;gap:10px}
.footer-brand .brand-dot{border-color:#eee;width:44px;height:44px}
.footer-brand .brand-name{color:var(--white);font-size:21px}
.footer-follow{left:228px;top:132px;width:107px;text-align:center;font-family:"Open Sans",Arial,sans-serif;font-size:11px;font-weight:700}
.footer-social{left:216px;top:165px}
.footer-social span{background:#8f7fb0}
.footer-col h5{font-family:"Open Sans",Arial,sans-serif;font-size:11px;font-weight:700;letter-spacing:.3px;margin-bottom:12px}
.footer-col li{list-style:none;font-size:11.5px;line-height:25.5px;color:#e6e6e6;white-space:nowrap}
.contact{left:466px;top:48px}
.menu{left:710px;top:48px}
.menu li{font-size:11px}
.newsletter{left:847px;top:48px;width:221px}
.newsletter .field{height:41px;background:var(--white);color:#555;font-size:11.5px;padding:13px 14px}
.newsletter .signup{margin-top:17px;height:49px;background:var(--lavender);color:#333;font-family:"Open Sans",Arial,sans-serif;font-weight:700;font-size:19px;display:flex;align-items:center;justify-content:center}
.copyright{left:0;top:2628px;width:1200px;height:43px;background:var(--lavender);font-size:10px;color:#333;display:flex;align-items:center;justify-content:center}
</style>
</head>
<body>

<div class="abs hero-photo" role="img" aria-label="Photo of two consultants reviewing work at a laptop in an office"></div>

<header class="abs site-header">
  <div class="abs brand"><span class="brand-dot"></span><span class="brand-name">Bright Harbor Venture</span></div>
  <span class="abs follow-label">FOLLOW US ON :</span>
  <div class="abs social header-social"><span></span><span></span><span></span><span></span></div>
  <div class="abs search">
    <svg width="8" height="8" viewBox="0 0 10 10"><circle cx="4" cy="4" r="3" fill="none" stroke="#999" stroke-width="1.3"/><path d="M6.2 6.2L9 9" stroke="#999" stroke-width="1.3"/></svg>SEARCH
  </div>
  <div class="abs menu-toggle"><span></span><span></span><span></span></div>
</header>

<div class="abs hero-caption">
  <h1>CONSULTING COMPANY</h1>
  <p>But I must explain to you how all this mistaken idea of denouncing pleasure and praising.</p>
</div>
<div class="abs slider-dots"><span></span><span class="active"></span><span></span><span></span><span></span></div>

<div class="abs cards-panel"></div>
<article class="abs card" style="left:144px">
  <div class="card-photo" role="img" aria-label="Portrait photo of a smiling businessman" style="background:linear-gradient(135deg,#f2f2f2,#c9ccd2)"></div>
  <h3>Professional and Personal</h3>
  <p>At vero eos et accusamus et iusto odio dignissimos ducimus.</p>
  <span class="read-more">READ MORE &#9656;</span>
</article>
<article class="abs card" style="left:452px">
  <div class="card-photo" role="img" aria-label="Photo of a group of business leaders standing together" style="background:linear-gradient(180deg,#b8c2cf,#3a3f4a)"></div>
  <h3>Next Generation Leaders</h3>
  <p>At vero eos et accusamus et iusto odio dignissimos ducimus.</p>
  <span class="read-more">READ MORE &#9656;</span>
</article>
<article class="abs card" style="left:760px">
  <div class="card-photo" role="img" aria-label="Photo of a team meeting around a table" style="background:linear-gradient(135deg,#d6cfc8,#8f8f9a)"></div>
  <h3>Consultation Options</h3>
  <p>At vero eos et accusamus et iusto odio dignissimos ducimus.</p>
  <span class="read-more">READ MORE &#9656;</span>
</article>

<section class="abs features" role="img" aria-label="Photo of a presenter holding a tablet in front of an audience">
  <div class="abs features-shade"></div>
  <div class="abs features-copy">
    <h2>OUR FEATURES</h2>
    <h4>BUT I MUST EXPLAIN TO YOU HOW ALL THIS</h4>
    <p>At vero eos et accusamus et iusto odio dignissimos ducimus qui blanditiis praesentium voluptatum.</p>
  </div>
  <div class="abs watch-btn">WATCH NOW</div>
  <svg class="abs play" width="100" height="100" viewBox="0 0 100 100"><circle cx="50" cy="50" r="44" fill="none" stroke="#d0202a" stroke-width="9"/><path d="M38 30L70 50L38 70Z" fill="#d0202a"/></svg>
</section>

<section class="abs welcome">
  <div class="abs welcome-copy">
    <h2>WELCOME TO OUR SITE</h2>
    <p>If you seek an experienced and trusted partner to work with you on an assignment or simply want some strategies to move your personal or professional talents to the next level then you are in the right place.</p>
    <p>If you feel that the pace of change in business is so fast that to be an outstanding leader you should ensure you are brought up to speed regularly then you are in the right place.</p>
    <p>If you are hearing about the essential new leadership essentials and you are ready to hear how to adopt them into your life or business then you are at the right place.</p>
    <p>I am so convinced that you will be delighted with how fast you can make change happen.</p>
  </div>
  <div class="abs welcome-photo" role="img" aria-label="Photo of a coach presenting at a whiteboard to a small group"></div>
</section>

<h2 class="abs section-title" style="top:1643px">ON ASSIGNMENT</h2>
<div class="abs assignment" style="left:134px">
  <div class="assignment-photo" role="img" aria-label="Overhead photo of a team working around a desk" style="background:linear-gradient(135deg,#cfd2d6,#4a4d52)"></div>
  <div class="assignment-caption">Team Cohesion Strategy</div>
</div>
<div class="abs assignment" style="left:456px">
  <div class="assignment-photo" role="img" aria-label="Photo of a man drawing business sketches on a wall" style="background:linear-gradient(135deg,#f4f4f4,#b5b5b5)"></div>
  <div class="assignment-caption">Go To Market Strategy</div>
</div>
<div class="abs assignment" style="left:775px">
  <div class="assignment-photo" role="img" aria-label="Photo of a businessman with a glowing world map" style="background:linear-gradient(135deg,#9db6d4,#2d4a72)"></div>
  <div class="assignment-caption">Internationalisation Strategy</div>
</div>

<section class="abs private-client"></section>
<h2 class="abs section-title" style="top:2040px">PRIVATE CLIENT</h2>

<div class="abs service-icon" style="left:139px">
  <svg width="70" height="70" viewBox="0 0 70 70" fill="none" stroke="#444" stroke-width="3" stroke-linejoin="round"><path d="M10 28h10l22-12v36L20 40H10z"/><path d="M16 40l4 14h6l-3-14"/><path d="M50 26l8-6M52 34h9M50 42l8 6"/></svg>
</div>
<div class="abs service-icon" style="left:392px">
  <svg width="70" height="70" viewBox="0 0 70 70"><circle cx="30" cy="17" r="9" fill="#444"/><circle cx="45" cy="27" r="8" fill="#444"/><text x="30" y="21" font-size="11" font-family="Roboto,sans-serif" fill="#e4daeb" text-anchor="middle" font-weight="700">$</text><text x="45" y="31" font-size="10" font-family="Roboto,sans-serif" fill="#e4daeb" text-anchor="middle" font-weight="700">$</text><path d="M10 42h9l10 4h12a3 3 0 010 6H30l14 0 12-8a3 3 0 014 4L46 60H20l-10-4z" fill="#444"/></svg>
</div>
<div class="abs service-icon" style="left:650px">
  <svg width="70" height="70" viewBox="0 0 70 70" fill="#444"><rect x="14" y="10" width="26" height="50"/><rect x="42" y="24" width="16" height="36"/><g fill="#e4daeb"><rect x="19" y="16" width="5" height="6"/><rect x="30" y="16" width="5" height="6"/><rect x="19" y="27" width="5" height="6"/><rect x="30" y="27" width="5" height="6"/><rect x="19" y="38" width="5" height="6"/><rect x="30" y="38" width="5" height="6"/><rect x="46" y="30" width="8" height="5"/><rect x="46" y="40" width="8" height="5"/><rect x="24" y="50" width="6" height="10"/></g></svg>
</div>
<div class="abs service-icon" style="left:928px">
  <svg width="70" height="70" viewBox="0 0 70 70" fill="none" stroke="#444" stroke-width="3"><circle cx="35" cy="35" r="24"/><ellipse cx="35" cy="35" rx="10" ry="24"/><path d="M11 35h48M15 23h40M15 47h40M35 11v48"/></svg>
</div>

<p class="abs service-label" style="left:78px">Promotion and<br>cash-buyer matching</p>
<p class="abs service-label" style="left:331px">Investment:<br>high return projects</p>
<p class="abs service-label" style="left:589px">Commercial:<br>Hotels and Senior Housing</p>
<p class="abs service-label" style="left:867px">Prestige Residential:<br>US, Australia, UK</p>

<footer class="abs site-footer">
  <div class="abs footer-brand"><span class="brand-dot"></span><span class="brand-name">Bright Harbor Venture</span></div>
  <div class="abs footer-follow">FOLLOW US</div>
  <div class="abs social footer-social"><span></span><span></span><span></span><span></span></div>

  <div class="abs footer-col contact">
    <h5>CONTACT US</h5>
    <ul>
      <li>418 Larkspur Avenue</li>
      <li>San Mateo, CA 94401</li>
      <li>Email: director@brightharborventure.com</li>
      <li>Call: +44 (0) 768 213 5597</li>
    </ul>
  </div>
  <div class="abs footer-col menu">
    <h5>MENU</h5>
    <ul>
      <li>About You</li>
      <li>About Us</li>
      <li>Our Values</li>
      <li>Testimonials</li>
      <li>Social Media</li>
      <li>News Alert</li>
    </ul>
  </div>
  <div class="abs footer-col newsletter">
    <h5>NEWSLETTER SIGNUP!</h5>
    <div class="field">E mail id</div>
    <div class="signup">SIGNUP!</div>
  </div>
</footer>
<div class="abs copyright">Copyrights @ 2016 All Rights Reserved</div>

</body>
</html>
```